Business Card Design: recruitment/consultancy for business Thrive360onward

We need a business card design for a new company based in Adelaide Australia called Thrive360onward. Our Business aims to support people over 50 who may be looking for a career change, have been made redundant or generally looking for employment. We will also be working with businesses to provide them with recruiting solutions, job design, recruitment strategies and customised training. we will also be working with volunteering opportunities for those over 50.
We would like to see the E in thrive360onward strong and dominant. The final design should reflect change for the better, better opportunities, today is the day, make way for the new, all aimed at the 50 plus age group.
Colours we are thinking off include green (money, growth) black and white.... we like the idea of black and white photography with a one dominant colour...think of a of a black and white photo of a woman with dominant red lips...that sort of look

Business

Contact Information for Business Card

Kim, Mavis & Gwen
phone: 0439615028
Thrive360onward@mailbox-example.net
Facebook/Thrive360onward
www.thrive360onward-example.com.au

```html
<!DOCTYPE html>
<html lang="en">
<head>
<meta charset="utf-8">
<title>Thrive360onward Business Card</title>
<link rel="stylesheet" href="https://fonts.googleapis.com/css2?family=Cinzel:wght@400&family=Open+Sans:wght@300;400&display=swap">
<style>
  :root {
    --page: #e9e8e4;
    --card: #ffffff;
    --ink: #2b2b2b;
    --muted: #5d5d5d;
    --band: #1c1c1c;
    --green: #6cc04a;
    --photo-dark: #151515;
    --photo-mid: #5a5a5a;
    --photo-light: #d6d6d6;
  }
  html, body {
    margin: 0;
    width: 1200px;
    height: 858px;
    overflow: hidden;
    background: var(--page);
  }
  .canvas {
    position: relative;
    width: 1200px;
    height: 858px;
  }
  .card {
    position: absolute;
    left: 250px;
    width: 700px;
    height: 400px;
    background: var(--card);
    box-shadow: 0 6px 18px rgba(0,0,0,0.18);
    overflow: hidden;
  }
  .card--front { top: 19px; }
  .card--back { top: 439px; }
  .card svg { display: block; }
  .brand {
    font-family: "Cinzel", serif;
    fill: var(--ink);
    letter-spacing: 1px;
  }
  .partners {
    font-family: "Open Sans", sans-serif;
    font-weight: 300;
    fill: var(--ink);
  }
  .contact-text {
    font-family: "Open Sans", sans-serif;
    font-weight: 400;
    font-size: 15px;
    fill: var(--muted);
  }
  .social-handle {
    font-family: "Open Sans", sans-serif;
    font-weight: 400;
    font-size: 20px;
    fill: #ffffff;
  }
</style>
</head>
<body>
<div class="canvas">

  <!-- Front of card -->
  <div class="card card--front">
    <svg width="700" height="400" viewBox="0 0 700 400">
      <defs>
        <linearGradient id="portraitTone" x1="0" y1="0" x2="1" y2="1">
          <stop offset="0" stop-color="var(--photo-dark)"/>
          <stop offset="0.55" stop-color="var(--photo-mid)"/>
          <stop offset="1" stop-color="var(--photo-light)"/>
        </linearGradient>
      </defs>

      <path class="portrait" role="img" aria-label="Black and white portrait photograph of a woman with red lips"
            fill="url(#portraitTone)"
            d="M410,0 H700 V30 C610,68 560,105 535,165 C528,180 510,185 490,185 L410,185 Z"/>

      <path class="swoosh-band" fill="var(--band)"
            d="M700,30 C600,70 550,120 520,210 S470,370 400,400 H700 Z"/>
      <path class="swoosh-gap" fill="none" stroke="var(--card)" stroke-width="16"
            d="M700,30 C600,70 550,120 520,210 S470,370 400,400"/>
      <path class="swoosh-green" fill="none" stroke="var(--green)" stroke-width="8"
            d="M700,30 C600,70 550,120 520,210 S470,370 400,400"/>

      <g class="logo-line">
        <text class="brand" x="50" y="222" font-size="22">THRIVE360ONWARD</text>
        <line x1="315" y1="200" x2="315" y2="228" stroke="var(--ink)" stroke-width="1.2"/>
        <text class="partners" x="328" y="222" font-size="18">Kim, Mavis &amp; Gwen</text>
      </g>

      <g class="contacts">
        <g class="contact contact--phone">
          <rect x="52" y="258" width="13" height="13" rx="2" fill="var(--muted)"/>
          <rect x="55" y="261" width="7" height="4" fill="var(--card)"/>
          <text class="contact-text" x="78" y="270">0439615028</text>
        </g>
        <g class="contact contact--email">
          <rect x="52" y="287" width="14" height="10" fill="none" stroke="var(--muted)" stroke-width="1.5"/>
          <polyline points="52,287 59,293 66,287" fill="none" stroke="var(--muted)" stroke-width="1.5"/>
          <text class="contact-text" x="78" y="297">Thrive360onward@mailbox-example.net</text>
        </g>
        <g class="contact contact--social">
          <circle cx="59" cy="319" r="6.5" fill="var(--muted)"/>
          <text class="contact-text" x="78" y="324">Facebook/Thrive360onward</text>
        </g>
        <g class="contact contact--web">
          <circle cx="59" cy="346" r="6.5" fill="none" stroke="var(--muted)" stroke-width="1.5"/>
          <line x1="52.5" y1="346" x2="65.5" y2="346" stroke="var(--muted)" stroke-width="1"/>
          <ellipse cx="59" cy="346" rx="2.8" ry="6.5" fill="none" stroke="var(--muted)" stroke-width="1"/>
          <text class="contact-text" x="78" y="351">www.thrive360onward-example.com.au</text>
        </g>
      </g>
    </svg>
  </div>

  <!-- Back of card -->
  <div class="card card--back">
    <svg width="700" height="400" viewBox="0 0 700 400">
      <defs>
        <radialGradient id="faintPortrait" cx="0.5" cy="0.5" r="0.5">
          <stop offset="0" stop-color="#9a9a9a"/>
          <stop offset="1" stop-color="#cfcfcf"/>
        </radialGradient>
      </defs>

      <path class="faint-portrait" role="img" aria-label="Faded black and white photograph of a woman in a wide hat"
            fill="url(#faintPortrait)" opacity="0.55"
            d="M140,70 C170,30 250,20 300,45 C345,70 340,140 320,180 C300,225 230,240 185,225 C140,210 110,160 120,120 C125,100 130,85 140,70 Z"/>

      <text class="brand" x="400" y="222" font-size="30" text-anchor="middle">THRIVE360ONWARD</text>

      <path class="swoosh-band" fill="var(--band)"
            d="M0,250 C120,300 200,345 330,365 S520,392 700,400 H0 Z"/>
      <path class="swoosh-gap" fill="none" stroke="var(--card)" stroke-width="16"
            d="M0,250 C120,300 200,345 330,365 S520,392 700,400"/>
      <path class="swoosh-green" fill="none" stroke="var(--green)" stroke-width="8"
            d="M0,250 C120,300 200,345 330,365 S520,392 700,400"/>

      <g class="social">
        <circle cx="42" cy="353" r="7" fill="var(--green)"/>
        <text class="social-handle" x="58" y="360">Thrive360onward</text>
      </g>
    </svg>
  </div>

</div>
</body>
</html>
```